Redesign and move to Wordpress for corvandel.com

Our website needs a redesign and at the same time we are moving it to Wordpress. Please help us with a new digital professional look and feel.

We are an Australian Software Engineering company specialising in advanced software development using in A.I., PLatform Engineering, Integration and Cloud. See the current corvandel.com for more information about us.

```html
<!DOCTYPE html>
<html lang="en">
<head>
<meta charset="utf-8">
<title>Corvandel — Reliable Smart Software Engineering</title>
<link href="https://fonts.googleapis.com/css2?family=Lato:wght@400;700;900&family=Montserrat:wght@500;600;700;800;900&display=swap" rel="stylesheet">
<style>
:root{
  --blue:#1a73e8;
  --blue-btn:#1877f2;
  --ink:#111318;
  --ink-2:#16181d;
  --panel:#25282e;
  --text:#222428;
  --muted:#4a4d55;
  --light:#f3f5f9;
  --line:#d9dee7;
  --white:#ffffff;
}
*{box-sizing:border-box;margin:0;padding:0}
html,body{width:1200px;height:4808px;overflow:hidden}
body{font-family:'Lato',sans-serif;color:var(--text);background:var(--white)}
section,header,footer,.band{position:relative;width:1200px;overflow:hidden}
.abs{position:absolute}
a{color:inherit;text-decoration:none}
.btn{position:absolute;display:flex;align-items:center;justify-content:center;gap:8px;background:var(--blue-btn);color:var(--white);font-family:'Lato',sans-serif;font-weight:700;font-size:14px;border-radius:3px}
.btn svg{width:9px;height:9px}
.eyebrow{position:absolute;left:0;width:1200px;text-align:center;font-family:'Montserrat',sans-serif;font-weight:700;font-size:20px;color:var(--blue);letter-spacing:.5px}
.sec-title{position:absolute;left:0;width:1200px;text-align:center;font-family:'Montserrat',sans-serif;font-weight:700;font-size:31px}

/* top bar */
.topbar{height:35px;background:var(--ink)}
.topbar .tag{left:112px;top:10px;font-size:12px;color:#e8e8e8}
.topbar .socials{right:112px;top:9px;display:flex;gap:14px;font-size:12px;color:#e8e8e8}
.topbar .socials span{display:flex;align-items:center;gap:5px}
.sq{display:inline-block;width:10px;height:10px;background:#e8e8e8;border-radius:2px}

/* nav */
.nav{height:92px;background:var(--white);border-bottom:1px solid #eee}
.brand{display:flex;align-items:center;gap:14px;font-family:'Montserrat',sans-serif;font-weight:500;letter-spacing:1px}
.brand .mark{display:inline-block;border:3px solid currentColor;border-radius:2px}
.nav .brand{left:110px;top:27px;font-size:29px;color:#1f2a44}
.nav .brand .mark{width:34px;height:34px;border-color:var(--blue)}
.nav .links{left:407px;top:37px;display:flex;gap:30px;font-size:14px;font-weight:700;color:#1f2a44}
.nav .links .on{color:var(--blue)}
.nav .search{left:912px;top:38px}
.nav .demo{left:959px;top:64px;width:129px;height:33px;top:64px}

/* hero */
.hero{height:461px;background:linear-gradient(100deg,#0b1330 0%,#13204a 35%,#0d1632 60%,#1a1e28 100%)}
.hero .photo{inset:0;background:radial-gradient(ellipse at 75% 40%,rgba(70,110,190,.35),transparent 60%),radial-gradient(ellipse at 95% 70%,rgba(20,20,25,.7),transparent 50%)}
.hero h1{left:110px;top:78px;font-family:'Montserrat',sans-serif;font-weight:900;font-size:49px;line-height:51px;color:var(--white);letter-spacing:.5px}
.hero p{left:110px;top:257px;font-size:20px;line-height:26px;color:var(--white)}
.hero .btn{left:110px;top:341px;width:131px;height:32px}

/* about */
.about{height:422px;background:var(--ink)}
.about .photo{left:112px;top:86px;width:444px;height:256px;background:linear-gradient(120deg,#5a4a3c,#8a7a66 40%,#3c3f46 75%,#23262c)}
.about h2{left:601px;top:81px;font-family:'Montserrat',sans-serif;font-weight:700;font-size:30px;color:var(--white)}
.about .lead{left:601px;top:137px;width:490px;font-size:14px;line-height:21px;color:#cfd2d8}
.about .checks{left:601px;top:221px;display:grid;grid-template-columns:245px 245px;row-gap:14px;font-size:15px;color:#dfe2e8}
.about .checks span{display:flex;align-items:center;gap:9px}
.tick{width:15px;height:15px}
.about .btn{left:601px;top:308px;width:134px;height:32px}

/* trusted */
.trusted{height:311px;background:var(--light)}
.trusted .eyebrow{top:83px;font-weight:500;font-size:21px}
.trusted .logos{left:110px;top:160px;width:980px;display:flex;justify-content:space-between;align-items:center}
.trusted .logo{display:flex;align-items:center;gap:10px;font-family:'Montserrat',sans-serif;font-weight:700;font-size:36px;color:#4b4e56}
.trusted .logo i{display:inline-block;width:30px;height:30px;background:#9aa0ab}
.trusted .logo i.c{border-radius:50%}

/* offer */
.offer{height:1028px;background:var(--white)}
.offer .eyebrow{top:92px}
.offer .sec-title{top:140px}
.card{position:absolute;width:304px;height:308px;background:var(--white);box-shadow:0 2px 10px rgba(0,0,0,.12);text-align:center}
.card.sel{box-shadow:none;border:1.5px dashed #6b8fd6}
.card svg.ic{position:absolute;left:50%;top:28px;width:64px;height:64px;margin-left:-32px}
.card h3{position:absolute;left:0;right:0;top:107px;font-family:'Montserrat',sans-serif;font-weight:700;font-size:19px;line-height:26px;color:var(--blue)}
.card p{position:absolute;left:28px;right:28px;top:166px;font-size:14px;line-height:20px;color:#333}
.card .btn{left:80px;top:248px;width:145px;height:32px}
.card.sel .btn{background:var(--white);color:var(--blue);border:2px solid var(--blue)}
.offer .more{left:535px;top:911px;width:130px;height:32px;border:2px solid #1f2a44;border-radius:3px;display:flex;align-items:center;justify-content:center;gap:8px;font-weight:700;font-size:15px;color:#1f2a44}

/* blog */
.blog{height:989px;background:var(--ink)}
.blog .eyebrow{top:94px}
.blog .sec-title{top:146px;color:var(--white)}
.blog .panel{left:112px;top:250px;width:976px;height:651px;background:var(--white)}
.post{position:absolute;top:26px;width:450px}
.post .img{width:450px;height:252px;background:linear-gradient(135deg,#0f1b30,#1f3d66 50%,#0c1424)}
.post h4{margin-top:26px;font-family:'Montserrat',sans-serif;font-weight:700;font-size:19px;color:var(--blue)}
.post .sub{margin-top:14px;font-size:13px;color:var(--blue)}
.post .body{margin-top:12px;font-size:13.6px;line-height:25.7px;color:#333}
.post .btn{position:relative;margin-top:18px;width:145px;height:32px}
.blog .dots{left:0;width:976px;top:609px;display:flex;justify-content:center;gap:14px}
.blog .dots i{width:11px;height:11px;border-radius:50%;background:#c4c8cf}
.blog .dots i.on{background:var(--blue)}

/* connect */
.connect{height:868px;background:var(--white)}
.connect .eyebrow{top:92px}
.connect .sec-title{top:142px}
.connect .box{left:112px;top:243px;width:976px;height:590px;border:2px solid #9cbdf2;border-radius:6px}
.box .left{left:0;top:0;width:362px;height:586px;border-right:1px solid var(--line)}
.avatar{left:40px;top:42px;width:66px;height:66px;border-radius:50%;background:linear-gradient(135deg,#3a3a3e,#7a6a5e)}
.box .who{left:133px;top:44px}
.who b{display:block;font-family:'Montserrat',sans-serif;font-weight:600;font-size:25px;color:var(--blue)}
.who span{display:block;margin-top:6px;font-size:13px;color:var(--blue)}
.box .dur{left:40px;top:160px;display:flex;align-items:center;gap:14px;font-size:19px;color:#222}
.box .tz{left:40px;top:222px;width:290px;height:44px;border:1px solid #555;border-radius:3px;display:flex;align-items:center;justify-content:space-between;padding:0 16px;font-size:18px}
.box .note{left:40px;top:312px;width:290px;font-size:19px;line-height:31px;color:#222}
.note em{font-style:normal;color:var(--blue)}
.cal{left:398px;top:0;width:370px}
.cal .month{position:absolute;left:0;top:36px;font-family:'Montserrat',sans-serif;font-weight:600;font-size:25px}
.cal .arrows{position:absolute;left:260px;top:40px;display:flex;gap:22px}
.cal .grid{position:absolute;left:-8px;top:92px;display:grid;grid-template-columns:repeat(7,50px);row-gap:13px;text-align:center;font-size:17px}
.cal .grid .h{font-size:14px;color:#333}
.cal .grid .b{color:var(--blue)}
.cal .grid .today{justify-self:center;width:34px;height:34px;margin-top:-7px;line-height:34px;border-radius:50%;background:#cfe0fb;color:var(--blue)}
.cal .hint{position:absolute;left:0;top:350px;width:320px;font-size:19px;line-height:31px;color:#222}
.cal .btn{left:8px;top:470px;width:230px;height:42px;font-family:'Montserrat',sans-serif;font-size:14px;letter-spacing:.5px}
.slots{left:765px;top:36px;width:210px}
.slots .date{font-family:'Montserrat',sans-serif;font-weight:500;font-size:24px;margin-bottom:24px}
.slots .s{height:41px;margin-bottom:10.5px;border:1.5px solid #9cbdf2;border-radius:2px;display:flex;align-items:center;justify-content:center;font-size:14px;color:var(--blue)}
.slots .s.on{background:var(--blue-btn);color:var(--white);border-color:var(--blue-btn)}

/* contact band */
.band{height:209px;background:var(--ink-2)}
.band .call{left:0;top:86px;width:506px;height:123px;background:var(--panel);clip-path:polygon(0 0,450px 0,506px 123px,0 123px)}
.band .phone{left:112px;top:104px;display:flex;align-items:center;gap:20px;font-size:21px;color:var(--white)}
.band .phone .circle{width:52px;height:52px;border-radius:50%;background:#2c6fe0;display:flex;align-items:center;justify-content:center}
.band .support{left:112px;top:164px;font-size:14px;color:#e6e6e6}
.band h3{left:622px;top:98px;font-family:'Montserrat',sans-serif;font-weight:700;font-size:31px;color:var(--white)}
.band .subnote{left:808px;top:114px;font-size:15px;color:#e6e6e6}
.band .email{left:625px;top:153px;width:297px;height:38px;border:1px solid #8a8d94;border-radius:3px;padding:0 26px;display:flex;align-items:center;font-size:14px;color:#aaa}
.band .btn{left:937px;top:153px;width:151px;height:38px;font-size:17px}

/* footer */
.footer{height:393px;background:var(--ink-2)}
.footer .brand{left:112px;top:53px;font-size:38px;color:var(--white)}
.footer .brand .mark{width:52px;height:52px}
.footer .about-f{left:112px;top:145px;width:360px;font-size:15px;line-height:25px;color:#e6e6e6}
.fcol{position:absolute;top:62px}
.fcol h5{font-family:'Montserrat',sans-serif;font-weight:700;font-size:24px;color:var(--white);margin-bottom:34px}
.fcol li{list-style:none;font-size:15px;line-height:31px;color:#e6e6e6}
.fcol.soc li{font-size:20px;line-height:41px;color:var(--blue);display:flex;align-items:center;gap:9px}
.fcol.soc .sq{width:16px;height:16px;background:var(--blue)}
.footer .copy{left:0;width:1200px;top:340px;text-align:center;font-size:14px;color:#cfcfcf}
</style>
</head>
<body>

<div class="band topbar" style="height:35px;background:var(--ink)">
  <div class="abs tag">Where Ideas Meet Intelligent Engineering.</div>
  <div class="abs socials"><span><i class="sq"></i>Folkspace</span><span><i class="sq"></i>Snapgrid</span><span><i class="sq"></i>Workhub</span></div>
</div>

<header class="nav">
  <div class="abs brand"><i class="mark"></i>corvandel</div>
  <nav class="abs links"><a class="on">Home</a><a>About us</a><a>Services</a><a>Blog</a><a>Contact us</a></nav>
  <svg class="abs search" width="16" height="16" viewBox="0 0 16 16"><circle cx="6.5" cy="6.5" r="5" fill="none" stroke="#1f2a44" stroke-width="2"/><line x1="10.2" y1="10.2" x2="15" y2="15" stroke="#1f2a44" stroke-width="2.2"/></svg>
  <a class="btn demo" style="left:959px;top:29px;width:129px;height:33px">
    <svg viewBox="0 0 10 12" style="width:10px;height:12px"><path d="M5 1a3.3 3.3 0 0 0-2 6v2h4V7a3.3 3.3 0 0 0-2-6z" fill="none" stroke="#fff" stroke-width="1.3"/><line x1="3.5" y1="11" x2="6.5" y2="11" stroke="#fff" stroke-width="1.3"/></svg>Free Demo</a>
</header>

<section class="hero">
  <div class="abs photo" role="img" aria-label="Photo of engineers working at monitors in a dark, blue-lit office"></div>
  <h1 class="abs">RELIABLE<br>SMART SOFTWARE<br>ENGINEERING</h1>
  <p class="abs">Innovation Starts Here<br>Custom Software for Your Unique Goals.</p>
  <a class="btn">Learn more <svg viewBox="0 0 8 10"><path d="M2 1l4 4-4 4" fill="none" stroke="#fff" stroke-width="2"/></svg></a>
</section>

<section class="about">
  <div class="abs photo" role="img" aria-label="Photo of a smiling software team collaborating around a tablet"></div>
  <h2 class="abs">About Us</h2>
  <p class="abs lead">At Corvandel, we craft bespoke software solutions that are not available on the market. Partner with us to redefine what's possible with cutting-edge technology.</p>
  <div class="abs checks">
    <span><svg class="tick" viewBox="0 0 16 16"><circle cx="8" cy="8" r="8" fill="#1a73e8"/><path d="M4.5 8.2l2.3 2.3 4.5-4.6" fill="none" stroke="#fff" stroke-width="1.8"/></svg>Market-leading products</span>
    <span><svg class="tick" viewBox="0 0 16 16"><circle cx="8" cy="8" r="8" fill="#1a73e8"/><path d="M4.5 8.2l2.3 2.3 4.5-4.6" fill="none" stroke="#fff" stroke-width="1.8"/></svg>Process automation</span>
    <span><svg class="tick" viewBox="0 0 16 16"><circle cx="8" cy="8" r="8" fill="#1a73e8"/><path d="M4.5 8.2l2.3 2.3 4.5-4.6" fill="none" stroke="#fff" stroke-width="1.8"/></svg>Legacy system enablement</span>
    <span><svg class="tick" viewBox="0 0 16 16"><circle cx="8" cy="8" r="8" fill="#1a73e8"/><path d="M4.5 8.2l2.3 2.3 4.5-4.6" fill="none" stroke="#fff" stroke-width="1.8"/></svg>Advanced intelligent systems</span>
  </div>
  <a class="btn">Learn more <svg viewBox="0 0 8 10"><path d="M2 1l4 4-4 4" fill="none" stroke="#fff" stroke-width="2"/></svg></a>
</section>

<section class="trusted">
  <div class="eyebrow">Trusted by teams worldwide at innovative companies</div>
  <div class="abs logos">
    <span class="logo">Tessaro</span>
    <span class="logo"><i></i>Halvik</span>
    <span class="logo"><i></i>Quenby</span>
    <span class="logo"><i class="c"></i>Orvane</span>
  </div>
</section>

<section class="offer">
  <div class="eyebrow">WE OFFER</div>
  <h2 class="sec-title">Custom Solutions Tailored to Your Needs</h2>

  <div class="card" style="left:110px;top:205px">
    <svg class="ic" viewBox="0 0 64 64" fill="none" stroke="#1a73e8" stroke-width="1.6"><circle cx="12" cy="12" r="4"/><circle cx="32" cy="12" r="4"/><circle cx="52" cy="12" r="4"/><circle cx="12" cy="32" r="4"/><circle cx="32" cy="32" r="4"/><circle cx="52" cy="32" r="4"/><circle cx="12" cy="52" r="4"/><circle cx="32" cy="52" r="4"/><circle cx="52" cy="52" r="4"/><path d="M16 32h12M36 32h12M32 36v12"/></svg>
    <h3>ENTERPRISE SYSTEMS<br>INTEGRATION</h3>
    <p>Automate your business processes internally or externally to improve data quality and process efficiency</p>
    <a class="btn">Learn More <svg viewBox="0 0 8 10"><path d="M2 1l4 4-4 4" fill="none" stroke="#fff" stroke-width="2"/></svg></a>
  </div>
  <div class="card sel" style="left:450px;top:205px">
    <svg class="ic" viewBox="0 0 64 64" fill="none" stroke="#1a73e8" stroke-width="1.6"><circle cx="8" cy="32" r="4" fill="#1a73e8"/><circle cx="32" cy="12" r="4"/><circle cx="56" cy="32" r="4"/><circle cx="32" cy="52" r="4"/><circle cx="44" cy="32" r="3"/><path d="M12 32h28M20 32l12-20M20 32l12 20M47 32h5"/></svg>
    <h3>MICRO<br>SERVICES</h3>
    <p>Leverage Microservices Architecture to enable quick deployment, team productivity and more</p>
    <a class="btn">Learn More <svg viewBox="0 0 8 10"><path d="M2 1l4 4-4 4" fill="none" stroke="#1a73e8" stroke-width="2"/></svg></a>
  </div>
  <div class="card" style="left:784px;top:205px">
    <svg class="ic" viewBox="0 0 64 64" fill="none" stroke="#1a73e8" stroke-width="1.6"><path d="M18 40a10 10 0 0 1 0-20 14 14 0 0 1 27-2 10 10 0 0 1 1 22z"/><path d="M32 40v16M24 40v10M40 40v10"/><circle cx="32" cy="58" r="2"/><circle cx="24" cy="52" r="2"/><circle cx="40" cy="52" r="2"/></svg>
    <h3>PLATFORM<br>ENGINEERING</h3>
    <p>For organisations looking to manage the security and cost risks around their cloud infrastructure</p>
    <a class="btn">Learn More <svg viewBox="0 0 8 10"><path d="M2 1l4 4-4 4" fill="none" stroke="#fff" stroke-width="2"/></svg></a>
  </div>

  <div class="card" style="left:110px;top:551px">
    <svg class="ic" viewBox="0 0 64 64" fill="none" stroke="#1a73e8" stroke-width="1.6"><rect x="20" y="6" width="22" height="10" rx="2"/><rect x="8" y="26" width="22" height="10" rx="2"/><rect x="20" y="46" width="22" height="10" rx="2"/><path d="M31 16v6H19v4M30 31h16M42 26l8 5-8 5z" /><path d="M19 36v6h12v4"/></svg>
    <h3>INTEGRATION PLATFORM<br>AS A SERVICE</h3>
    <p>This is the new integration approach that enables quick, efficient and reliable enterprise systems integration</p>
    <a class="btn">Learn More <svg viewBox="0 0 8 10"><path d="M2 1l4 4-4 4" fill="none" stroke="#fff" stroke-width="2"/></svg></a>
  </div>
  <div class="card" style="left:450px;top:551px">
    <svg class="ic" viewBox="0 0 64 64" fill="none" stroke="#1a73e8" stroke-width="1.6"><path d="M22 58V44a16 16 0 1 1 22-6v6h-8v14"/><circle cx="32" cy="22" r="3"/><circle cx="40" cy="30" r="2.5"/><circle cx="26" cy="32" r="2.5"/><path d="M32 25v10M34 24l5 5M29 24l-3 6"/></svg>
    <h3>COPILOT /AI<br>AGENTS</h3>
    <p>Automate your business processes internally or externally to improve data quality and process efficiency</p>
    <a class="btn">Learn More <svg viewBox="0 0 8 10"><path d="M2 1l4 4-4 4" fill="none" stroke="#fff" stroke-width="2"/></svg></a>
  </div>
  <div class="card" style="left:784px;top:551px">
    <svg class="ic" viewBox="0 0 64 64" fill="none" stroke="#1a73e8" stroke-width="1.6"><path d="M32 8l4 6 7-2 1 7 7 2-3 6 5 5-6 4 2 7-7 1-2 7-6-3"/><circle cx="30" cy="34" r="9"/><path d="M40 50l12-12M48 38h4v4"/></svg>
    <h3>REAL-TIME DATA<br>STREAM PROCESSING</h3>
    <p>Able to react to changing business conditions in a precise intelligent way is becoming more important.</p>
    <a class="btn">Learn More <svg viewBox="0 0 8 10"><path d="M2 1l4 4-4 4" fill="none" stroke="#fff" stroke-width="2"/></svg></a>
  </div>

  <a class="abs more">See More <svg width="14" height="10" viewBox="0 0 14 10"><path d="M0 5h12M8 1l4 4-4 4" fill="none" stroke="#1f2a44" stroke-width="2"/></svg></a>
</section>

<section class="blog">
  <div class="eyebrow">OUR BLOG</div>
  <h2 class="sec-title">Updates from our industry</h2>
  <div class="abs panel">
    <article class="post" style="left:26px">
      <div class="img" role="img" aria-label="Illustration of a hand holding a phone with glowing AI interface panels"></div>
      <h4>BUSINESS INSIGHTS</h4>
      <div class="sub">How story telling hepls data-driven teams succeed</div>
      <p class="body">Winning leaders know that data alone isn't enough. It's the art of storytelling that drives sustained performance. In the spring of 2014, the Harbor City Comets hired Dale Marsh as their head coach. Despite a star-studded roster, they hadn't won a national league championship in 40 years. Marsh changed the system, combining talent with authentic storytelling.</p>
      <a class="btn">Read More <svg viewBox="0 0 8 10"><path d="M2 1l4 4-4 4" fill="none" stroke="#fff" stroke-width="2"/></svg></a>
    </article>
    <article class="post" style="left:500px">
      <div class="img" role="img" aria-label="Photo of hands on a laptop with floating data dashboards"></div>
      <h4>ARTIFICIAL INTELLIGENCE</h4>
      <div class="sub">Advancing updates on responsible AI Research</div>
      <p class="body">A surge of generative AI models in the past year has fueled much discussion about the impact of artificial intelligence on human history. Whether exploring impressive new capabilities of large language models (LLMs) such as Model-4 or examining the spectrum of machine learning techniques already embedded in our daily lives, researchers agree on the importance of transparency.</p>
      <a class="btn">Read More <svg viewBox="0 0 8 10"><path d="M2 1l4 4-4 4" fill="none" stroke="#fff" stroke-width="2"/></svg></a>
    </article>
    <div class="abs dots"><i class="on"></i><i></i><i></i><i></i><i></i></div>
  </div>
</section>

<section class="connect">
  <div class="eyebrow">LET'S CONNECT</div>
  <h2 class="sec-title">Schedule a consultation now</h2>
  <div class="abs box">
    <div class="abs left">
      <div class="abs avatar" role="img" aria-label="Portrait photo of the chief technical officer"></div>
      <div class="abs who"><b>Corvandel</b><span>Chief Technical Officer</span></div>
      <div class="abs dur"><svg width="20" height="24" viewBox="0 0 20 24"><path d="M2 2h16M2 22h16M4 2c0 7 12 7 12 10S4 15 4 22M16 2c0 7-12 7-12 10s12 3 12 10" fill="none" stroke="#1a73e8" stroke-width="2.2"/></svg>30 Minutes</div>
      <div class="abs tz">Australia (GMT+11)<span style="display:flex;align-items:center;gap:14px"><i style="width:1px;height:20px;background:#555"></i><svg width="14" height="9" viewBox="0 0 14 9"><path d="M1 1l6 6 6-6" fill="none" stroke="#222" stroke-width="2.2"/></svg></span></div>
      <p class="abs note">Book an obligation free <em>consultation</em> with our Lead Technologist today for personalized <em>support</em> and <em>guidance.</em></p>
    </div>
    <div class="abs cal">
      <div class="month">January</div>
      <div class="arrows"><svg width="12" height="18" viewBox="0 0 12 18"><path d="M10 2L3 9l7 7" fill="none" stroke="#bbb" stroke-width="2.5"/></svg><svg width="12" height="18" viewBox="0 0 12 18"><path d="M2 2l7 7-7 7" fill="none" stroke="#222" stroke-width="2.5"/></svg></div>
      <div class="grid">
        <span class="h">Sun</span><span class="h">Mon</span><span class="h">Tue</span><span class="h">Wed</span><span class="h">Thu</span><span class="h">Fri</span><span class="h">Sat</span>
        <span></span><span></span><span></span><span>1</span><span>2</span><span>3</span><span>4</span>
        <span>5</span><span>6</span><span>7</span><span>8</span><span>9</span><span>10</span><span>11</span>
        <span class="b">12</span><span class="b">13</span><span class="b">14</span><span class="b">15</span><span class="today">16</span><span class="b">15</span><span class="b">16</span>
        <span class="b">19</span><span class="b">20</span><span class="b">21</span><span class="b">22</span><span class="b">23</span><span class="b">24</span><span class="b">25</span>
        <span class="b">26</span><span class="b">27</span><span class="b">28</span><span class="b">29</span><span class="b">30</span><span class="b">31</span><span></span>
      </div>
      <p class="hint">You can choose your slot so that we can meet at your desirable and convenient timings.</p>
      <a class="btn">SCHEDULE MEET <svg viewBox="0 0 18 18" style="width:18px;height:18px"><rect x="2" y="3" width="14" height="13" rx="1.5" fill="none" stroke="#fff" stroke-width="1.6"/><path d="M2 7h14M6 1v4M12 1v4M6.5 11.5l2 2 3.5-3.5" fill="none" stroke="#fff" stroke-width="1.6"/></svg></a>
    </div>
    <div class="abs slots">
      <div class="date">Thu, Jan 16</div>
      <div class="s">10.00 AM</div><div class="s">12.00 PM</div><div class="s">13.30 PM</div><div class="s on">15.00 PM</div><div class="s">17.30 PM</div><div class="s">19.00 PM</div><div class="s">20.30 PM</div><div class="s">22.00 PM</div>
    </div>
  </div>
</section>

<div class="band">
  <div class="abs call"></div>
  <div class="abs phone"><span class="circle"><svg width="26" height="26" viewBox="0 0 24 24"><path d="M6.6 10.8a15 15 0 0 0 6.6 6.6l2.2-2.2c.3-.3.7-.4 1-.2 1.1.4 2.3.6 3.6.6.6 0 1 .4 1 1V20c0 .6-.4 1-1 1A17 17 0 0 1 3 4c0-.6.4-1 1-1h3.5c.6 0 1 .4 1 1 0 1.3.2 2.5.6 3.6.1.3 0 .7-.2 1z" fill="#fff"/></svg></span>1-800-555-0142</div>
  <div class="abs support">Our Support Service is always available 24/7</div>
  <h3 class="abs">Subscribe</h3>
  <div class="abs subnote">Get the latest updates and offers</div>
  <div class="abs email">Your E-mail</div>
  <a class="btn">Subscribe <svg viewBox="0 0 14 16" style="width:14px;height:16px"><path d="M7 1a4.5 4.5 0 0 0-4.5 4.5V10L1 12.5h12L11.5 10V5.5A4.5 4.5 0 0 0 7 1zM5 14a2 2 0 0 0 4 0z" fill="#fff"/></svg></a>
</div>

<footer class="footer">
  <div class="abs brand"><i class="mark"></i>corvandel</div>
  <p class="abs about-f">At Corvandel, we craft bespoke software solutions that are not available on the market. Partner with us to redefine what's possible with cutting-edge technology.</p>
  <div class="fcol" style="left:547px"><h5>Explore</h5><ul><li>Home</li><li>About us</li><li>Services</li><li>Blog</li></ul></div>
  <div class="fcol" style="left:730px"><h5>Useful Links</h5><ul><li>Privacy policy</li><li>Terms of service</li><li>Cookies</li><li>Support</li></ul></div>
  <div class="fcol soc" style="left:968px"><h5>Socials</h5><ul style="margin-top:-8px"><li><i class="sq"></i>Folkspace</li><li><i class="sq"></i>Snapgrid</li><li><i class="sq"></i>Workhub</li></ul></div>
  <div class="abs copy">© 2025 Corvandel. All Rights Reserved.</div>
</footer>

</body>
</html>
```